Werbebrief
Zielgruppe
Unsere Zielgruppe sind Geschäftsführer junger Unternehmen.
Hallo,
Wir benötigen einen "Werbebrief". Es ist jedoch weniger ein Brief, als viel mehr eine etwas größerer "Werbekarte" (diese soll 105 x 210mm groß sein).
Auf der Vorderseite soll folgender Text stehen:
Für Unternehmen, die gerne expandieren möchten
Auf der Rückseite soll folgender Link stehen:
www.feldrok-studio.de/Expandieren
Darunter soll folgendes stehen:
Ihr persönlicher Code: ABC123
Wichtig ist, dass wir den Code individuell ändern können, da jeder einen anderen Code bekommt.
Unser Logo und Corporate Farbe habe ich hochgeladen. Das Design sollte auf jeden Fall zu unserer Webseite passen (www.feldrok-studio.de)
Wir freuen uns auf Ihre Vorschläge.

```html
<!DOCTYPE html>
<html lang="de">
<head>
<meta charset="utf-8">
<title>Feldrok Studio – Werbekarte</title>
<link href="https://fonts.googleapis.com/css2?family=Jost:wght@400;500&display=swap" rel="stylesheet">
<style>
  :root {
    --stage: #e9e7e4;
    --card-blue: #1a4e8c;
    --ghost-blue: #4f77a8;
    --ink-white: #ffffff;
  }
  html, body {
    margin: 0;
    padding: 0;
    width: 1200px;
    height: 1143px;
    overflow: hidden;
    background: var(--stage);
    font-family: "Jost", "Futura", sans-serif;
  }
  .canvas {
    position: relative;
    width: 1200px;
    height: 1143px;
  }
  .card {
    position: absolute;
    left: 150px;
    width: 900px;
    height: 450px;
    background: var(--card-blue);
    color: var(--ink-white);
    overflow: hidden;
  }
  .card--front { top: 81px; }
  .card--back { top: 612px; }

  .rule-lines {
    position: absolute;
    inset: 0;
    width: 900px;
    height: 450px;
  }
  .rule-lines line {
    stroke: var(--ink-white);
    stroke-width: 2;
  }

  .ghost {
    position: absolute;
    margin: 0;
    color: var(--ghost-blue);
    font-weight: 400;
    text-transform: uppercase;
    letter-spacing: 0.02em;
    line-height: 1;
    white-space: nowrap;
  }

  .headline {
    position: absolute;
    left: 18px;
    top: 100px;
    margin: 0;
    font-size: 46px;
    line-height: 47px;
    font-weight: 500;
    text-transform: uppercase;
    letter-spacing: 0.02em;
  }
  .headline span { display: block; }

  .ghost--nehmen { left: 292px; top: 62px; font-size: 46px; }
  .ghost--expand-front { left: 172px; top: 196px; font-size: 46px; }

  .brand {
    position: absolute;
    left: 786px;
    writing-mode: vertical-rl;
    font-size: 26px;
    font-weight: 400;
    letter-spacing: 0.03em;
    white-space: nowrap;
  }
  .card--front .brand { top: 210px; }
  .card--back .brand { top: 190px; }

  .brand-mark {
    position: absolute;
    left: 788px;
    width: 20px;
    height: 20px;
    background: var(--ink-white);
  }
  .card--front .brand-mark { top: 150px; }
  .card--back .brand-mark { top: 128px; }

  .campaign-url {
    position: absolute;
    left: 60px;
    top: 148px;
    margin: 0;
    font-size: 29px;
    font-weight: 500;
    letter-spacing: 0.02em;
    white-space: nowrap;
  }
  .ghost--expand-back { left: 414px; top: 186px; font-size: 46px; }

  .personal-code {
    position: absolute;
    right: 148px;
    top: 318px;
    margin: 0;
    font-size: 31px;
    font-weight: 500;
    letter-spacing: 0.02em;
    white-space: nowrap;
  }
  .ghost--code { left: 418px; top: 356px; font-size: 46px; }
</style>
</head>
<body>
<main class="canvas">

  <section class="card card--front" aria-label="Vorderseite">
    <p class="ghost ghost--nehmen" aria-hidden="true">Nehmen</p>
    <p class="ghost ghost--expand-front" aria-hidden="true">Expandieren</p>
    <h1 class="headline">
      <span>Für Unter-</span>
      <span>nehmen,</span>
      <span>die</span>
      <span>gerne</span>
      <span>ex-</span>
      <span>pandieren</span>
      <span>möchten!</span>
    </h1>
    <svg class="rule-lines" viewBox="0 0 900 450" aria-hidden="true">
      <line x1="520" y1="200" x2="775" y2="200"/>
      <line x1="775" y1="200" x2="775" y2="410"/>
    </svg>
    <span class="brand-mark" aria-hidden="true"></span>
    <p class="brand" style="margin:0">Feldrok Studio</p>
  </section>

  <section class="card card--back" aria-label="Rückseite">
    <p class="ghost ghost--expand-back" aria-hidden="true">Expandieren</p>
    <p class="ghost ghost--code" aria-hidden="true">ABC123</p>
    <p class="campaign-url">www.feldrok-studio.de/Expandieren</p>
    <svg class="rule-lines" viewBox="0 0 900 450" aria-hidden="true">
      <line x1="596" y1="182" x2="775" y2="182"/>
      <line x1="775" y1="182" x2="775" y2="420"/>
    </svg>
    <p class="personal-code">Ihr persönlicher Code: <span class="code-value">ABC123</span></p>
    <span class="brand-mark" aria-hidden="true"></span>
    <p class="brand" style="margin:0">Feldrok Studio</p>
  </section>

</main>
</body>
</html>
```